Website Development for vaultmerrow.com.au

Build a new Wordpress/Responsive website for vaultmerrow.com.au

Target Market(s)

Compliance Managers, Risk Managers, Information Security and Cyber Security Professionals, Chief Data/Digital Officers, Chief Operating/Financial Officers, Business Continuity Professionals, Disaster Recovery Planners, Small Business Owners, Local/Federal Government entities

Industry/Entity Type

Data Service

Coding

Coded - Design and coding required

Number of Pages Required

5+ page

Font styles to use
Sans Serif

Colors

Designer to choose colors to be used in the design.

Requirements
Must have
• 1. Site Structure: Home Page plus the following chapter-pages for a) Services b) About c) Resources d) Blog e) Contact Us
• 2. Prefer site to built on wordpress and we can purchase a theme if needed (we currently use Kelp9 for other sites)
• 3. Blog needs to be wordpress based
• 4. We will host the site ourselves on our own servers
• 5. Responsive Design
Nice to have
• 1. Livechat capability/interface
• 2. Capability for marketing automation integration (such as hubspot, marketo, infusionsoft etc)
• 3. Capability for CRM integration (Salesforce)

```html
<!DOCTYPE html>
<html lang="en">
<head>
<meta charset="utf-8">
<title>Vaultmerrow – Home</title>
<link href="https://fonts.googleapis.com/css2?family=Poppins:wght@400;500;600;700;800&family=Open+Sans:wght@400;600;700&display=swap" rel="stylesheet">
<style>
:root{
  --red:#e3001b;
  --red-dark:#b80016;
  --pink:#fde4e6;
  --ink:#1c1c1c;
  --text:#555;
  --muted:#8a8a8a;
  --line:#e4e4e4;
  --grey-bg:#f1f1f3;
  --white:#fff;
  --navy:#0d2438;
  --steel:#5d7f98;
  --blue:#4a90d6;
  --fb:#3b5998;
  --tw:#1da1f2;
  --dark:#262626;
  --darker:#1b1b1b;
}
*{margin:0;padding:0;box-sizing:border-box}
html,body{width:1200px;height:5000px;overflow:hidden}
body{font-family:"Open Sans",Arial,sans-serif;color:var(--text);background:var(--white);position:relative;font-size:14px}
h1,h2,h3,h4,.nav,.btn{font-family:"Poppins",Arial,sans-serif}
.abs{position:absolute}
.btn{display:inline-block;background:var(--red);color:var(--white);font-weight:600;font-size:13px;letter-spacing:.5px;padding:11px 22px;border-radius:3px;text-transform:uppercase}
.btn-outline{display:inline-block;border:2px solid var(--red);color:var(--ink);font-family:"Poppins",sans-serif;font-weight:600;font-size:12px;padding:6px 14px;border-radius:3px}
.divider{display:flex;align-items:center;justify-content:center;gap:6px;margin-top:10px}
.divider span{display:block;width:28px;height:2px;background:var(--muted)}
.divider i{display:block;width:6px;height:6px;border-radius:50%;background:var(--red)}
.section-title{font-size:30px;font-weight:700;color:var(--ink);text-align:center;letter-spacing:.5px}

/* header */
.site-header{position:absolute;top:0;left:0;width:1200px;height:112px;background:var(--white)}
.brand{position:absolute;left:72px;top:22px;display:flex;align-items:center;gap:10px}
.brand-mark{width:34px;height:34px;background:var(--red);border-radius:50%}
.brand-name{font-family:"Poppins",sans-serif;font-weight:800;font-size:32px;color:var(--red);letter-spacing:1px;line-height:1}
.header-top{position:absolute;right:40px;top:18px;display:flex;align-items:center;gap:12px;font-size:12px;color:var(--ink);font-weight:600}
.social{width:26px;height:26px;border-radius:50%;display:inline-block}
.social.fb{background:var(--fb)}.social.tw{background:var(--tw)}
.phone-pill{border:2px solid var(--red);color:var(--red);border-radius:4px;padding:5px 14px;font-weight:700;margin-left:10px}
.nav{position:absolute;right:40px;top:72px;display:flex;gap:30px;font-size:13px;font-weight:600;color:var(--ink)}
.nav .active{color:var(--red);border-bottom:2px solid var(--red);padding-bottom:4px}

/* hero */
.hero{position:absolute;top:112px;left:0;width:1200px;height:700px;background:linear-gradient(100deg,#3f5e78 0%,#7795ad 35%,#c9d6e0 60%,#1e2530 80%,#0f1318 100%)}
.hero-copy{position:absolute;left:140px;top:170px;color:var(--white)}
.hero-copy h1{font-size:48px;font-weight:800;letter-spacing:1px}
.hero-copy p{font-size:21px;font-weight:600;width:430px;line-height:1.35;margin:14px 0 30px}
.hero-dots{position:absolute;left:560px;top:645px;display:flex;gap:10px}
.hero-dots i{width:10px;height:10px;border-radius:50%;background:rgba(255,255,255,.6)}
.hero-dots i.on{background:var(--red)}
.hero-curve{position:absolute;left:0;bottom:-1px}

/* services */
.services{position:absolute;top:812px;left:0;width:1200px;height:650px;background:var(--white)}
.service-grid{position:absolute;left:110px;top:80px;width:980px;display:grid;grid-template-columns:repeat(4,1fr);row-gap:70px}
.service{text-align:center;padding:0 22px}
.service-icon{width:62px;height:62px;border-radius:50%;background:var(--pink);margin:0 auto 22px;display:flex;align-items:center;justify-content:center}
.service h3{font-size:15px;font-weight:600;color:var(--ink);margin-bottom:10px}
.service p{font-size:11.5px;line-height:1.45;color:var(--muted)}
.service .more{display:block;margin-top:18px;font-family:"Poppins",sans-serif;font-size:11px;font-weight:700;color:var(--red)}

/* about */
.about{position:absolute;top:1430px;left:0;width:1200px;height:650px;background:var(--grey-bg)}
.about-copy{position:absolute;left:140px;top:150px;width:380px}
.about-copy h4{font-size:28px;font-weight:500;color:var(--ink);line-height:1.1}
.about-copy h2{font-size:30px;font-weight:800;color:var(--ink);line-height:1.1}
.about-copy .divider{justify-content:flex-start}
.about-copy p{font-size:12.5px;line-height:1.6;margin:24px 0 30px}
.about-visual{position:absolute;left:610px;top:100px;width:480px;height:470px;border-radius:0 0 240px 240px;background:linear-gradient(160deg,#dfe6ec,#8fa7bb 60%,#c7d4de)}

/* resources */
.resources{position:absolute;top:2080px;left:0;width:1200px;height:660px;background:var(--white)}
.resources-visual{position:absolute;left:140px;top:60px;width:440px;height:440px;background:radial-gradient(circle at 50% 45%,#2f7bd0 0%,#123e72 40%,#061426 80%)}
.resources-copy{position:absolute;left:630px;top:60px;width:430px}
.resources-copy h2{font-size:30px;font-weight:700;color:var(--ink)}
.resources-copy .divider{justify-content:flex-start}
.resources-copy p{font-size:12.5px;line-height:1.6;margin:20px 0 16px}
.resources-list{list-style:none;margin-bottom:26px}
.resources-list li{font-size:12.5px;line-height:2;padding-left:16px;position:relative}
.resources-list li:before{content:"";position:absolute;left:0;top:11px;width:6px;height:6px;border-radius:50%;background:var(--red)}

/* blog */
.blog{position:absolute;top:2740px;left:0;width:1200px;height:1000px;background:var(--grey-bg)}
.blog .section-title{position:absolute;top:80px;width:100%}
.blog .divider{position:absolute;top:126px;width:100%}
.card{position:absolute;background:var(--white);padding:22px}
.card h3{font-size:15px;font-weight:700;color:var(--ink);line-height:1.3}
.card p{font-size:12px;line-height:1.5;margin:10px 0 14px}
.card .tag{font-size:11px;color:var(--muted);margin-bottom:6px}
.card-photo{position:absolute;left:0;top:0;width:100%;height:200px;background:linear-gradient(180deg,#2f6e77,#163b45 60%,#0d1f26)}
.card.red{background:var(--red);color:var(--white)}
.card.red h3{color:var(--white);font-size:20px}
.card.blue{background:var(--blue);color:var(--white)}
.card.blue h3{color:var(--white);font-size:18px}
.card.dark{background:#2a2a2a;color:#ddd;text-align:center}
.card.dark h4{font-family:"Poppins",sans-serif;font-size:26px;color:var(--white);font-weight:500}
.card.dark h3{color:var(--white);font-size:22px;font-weight:500;width:440px;margin:14px auto 0}
.btn-white{display:inline-block;background:var(--white);color:var(--ink);font-family:"Poppins",sans-serif;font-weight:700;font-size:12px;padding:7px 16px;border-radius:3px}
.btn-ghost{display:inline-block;border:2px solid var(--white);color:var(--white);font-family:"Poppins",sans-serif;font-weight:700;font-size:12px;padding:6px 16px;border-radius:3px}
.view-all{position:absolute;left:525px;top:880px}

/* contact */
.contact{position:absolute;top:3740px;left:0;width:1200px;height:920px;background:var(--white)}
.contact .section-title{position:absolute;top:40px;width:100%}
.contact .divider{position:absolute;top:86px;width:100%}
.info-card{position:absolute;left:140px;top:150px;width:520px;height:740px;background:var(--white);box-shadow:0 4px 18px rgba(0,0,0,.12)}
.map{width:100%;height:310px;background:linear-gradient(135deg,#e9ecef,#d7dde2)}
.map-label{position:absolute;left:110px;top:100px;background:var(--white);padding:12px 16px;font-size:12px;color:var(--ink);box-shadow:0 2px 8px rgba(0,0,0,.2);line-height:1.5;display:flex;gap:10px;align-items:center}
.info-row{display:flex;gap:24px;align-items:flex-start;padding:30px 30px;border-bottom:1px solid var(--line);font-size:12.5px;line-height:1.6;color:var(--ink)}
.info-row:last-child{border-bottom:none}
.form-card{position:absolute;left:690px;top:130px;width:370px;height:740px;background:var(--white);box-shadow:0 4px 18px rgba(0,0,0,.12);padding:30px}
.form-card h3{font-size:17px;font-weight:700;color:var(--ink)}
.form-card .divider{position:static;justify-content:flex-start}
.field{border:1px solid #cfcfcf;height:38px;margin-top:14px;padding:10px 12px;font-size:10px;color:var(--muted);text-transform:uppercase}
.field.area{height:240px}
.submit{margin-top:28px;background:var(--red);color:var(--white);text-align:center;font-family:"Poppins",sans-serif;font-weight:700;font-size:22px;padding:10px 0;border-radius:3px}

/* footer */
.site-footer{position:absolute;top:4660px;left:0;width:1200px;height:340px;background:var(--dark);color:#ccc;text-align:center}
.footer-brand{position:absolute;top:60px;width:100%;display:flex;justify-content:center;align-items:center;gap:10px}
.footer-nav{position:absolute;top:150px;width:100%;display:flex;justify-content:center;gap:18px;font-family:"Poppins",sans-serif;font-size:12px;color:#ddd}
.footer-follow{position:absolute;top:200px;width:100%;display:flex;justify-content:center;align-items:center;gap:10px;font-size:12px;font-weight:600}
.copyright{position:absolute;bottom:0;width:100%;height:40px;line-height:40px;background:var(--darker);font-size:11px;color:#999}
</style>
</head>
<body>

<header class="site-header">
  <div class="brand"><span class="brand-mark"></span><span class="brand-name">VAULTMERROW</span></div>
  <div class="header-top">
    <span>FOLLOW US</span>
    <span class="social fb"></span><span class="social tw"></span>
    <svg width="18" height="18" viewBox="0 0 24 24" style="margin-left:14px"><path d="M6.6 10.8a15 15 0 0 0 6.6 6.6l2.2-2.2c.3-.3.7-.4 1-.2 1.1.4 2.3.6 3.6.6.6 0 1 .4 1 1V20c0 .6-.4 1-1 1A17 17 0 0 1 3 4c0-.6.4-1 1-1h3.5c.6 0 1 .4 1 1 0 1.3.2 2.5.6 3.6.1.3 0 .7-.2 1z" fill="#1c1c1c"/></svg>
    <span class="phone-pill">+1 (000) 000 0000</span>
  </div>
  <nav class="nav">
    <span class="active">HOME</span><span>SERVICES</span><span>ABOUT</span><span>RESOURCES</span><span>BLOG</span><span>CONTACT US</span>
  </nav>
</header>

<section class="hero" role="img" aria-label="Photo of a businessman in a suit holding a glowing security shield over a digital network background">
  <div class="hero-copy">
    <h1>CYBER SECURITY</h1>
    <p>Lorem Ipsum is simply dummy text of the printing and typesetting industry.</p>
    <span class="btn">Read More</span>
  </div>
  <div class="hero-dots"><i></i><i class="on"></i><i></i><i></i></div>
  <svg class="hero-curve" width="1200" height="90" viewBox="0 0 1200 90" preserveAspectRatio="none"><path d="M0 30 Q600 120 1200 30 L1200 90 L0 90 Z" fill="#fff"/></svg>
</section>

<section class="services">
  <h2 class="section-title" style="margin-top:40px">OUR SERVICES</h2>
  <div class="divider"><span></span><i></i><span></span></div>
  <div class="service-grid">
    <div class="service"><div class="service-icon"><svg width="26" height="26" viewBox="0 0 24 24"><path d="M12 2l8 3v7c0 5-3.5 8.5-8 10-4.5-1.5-8-5-8-10V5z" fill="#e3001b"/></svg></div><h3>Compliance</h3><p>Sed ut perspiciatis unde omnis iste natus error sit volupta accus antium dolore.</p><span class="more">READ MORE ›</span></div>
    <div class="service"><div class="service-icon"><svg width="26" height="26" viewBox="0 0 24 24"><circle cx="12" cy="12" r="9" fill="none" stroke="#e3001b" stroke-width="3"/><path d="M12 7v6l4 2" stroke="#e3001b" stroke-width="2.5" fill="none"/></svg></div><h3>Risk Management</h3><p>Sed ut perspiciatis unde omnis iste natus error sit volupta accus antium dolore.</p><span class="more">READ MORE ›</span></div>
    <div class="service"><div class="service-icon"><svg width="26" height="26" viewBox="0 0 24 24"><rect x="4" y="4" width="16" height="16" rx="3" fill="#e3001b"/><path d="M8 12l3 3 5-6" stroke="#fff" stroke-width="2" fill="none"/></svg></div><h3>Information Security</h3><p>Sed ut perspiciatis unde omnis iste natus error sit volupta accus antium dolore.</p><span class="more">READ MORE ›</span></div>
    <div class="service"><div class="service-icon"><svg width="26" height="26" viewBox="0 0 24 24"><rect x="5" y="11" width="14" height="10" rx="2" fill="#e3001b"/><path d="M8 11V8a4 4 0 0 1 8 0v3" stroke="#e3001b" stroke-width="2.5" fill="none"/></svg></div><h3>Cyber Security</h3><p>Sed ut perspiciatis unde omnis iste natus error sit volupta accus antium dolore.</p><span class="more">READ MORE ›</span></div>
    <div class="service"><div class="service-icon"><svg width="26" height="26" viewBox="0 0 24 24"><circle cx="12" cy="12" r="4" fill="#e3001b"/><circle cx="4" cy="5" r="2.5" fill="#e3001b"/><circle cx="20" cy="5" r="2.5" fill="#e3001b"/><circle cx="12" cy="21" r="2.5" fill="#e3001b"/></svg></div><h3>Data/Digital</h3><p>Sed ut perspiciatis unde omnis iste natus error sit volupta accus antium dolore.</p><span class="more">READ MORE ›</span></div>
    <div class="service"><div class="service-icon"><svg width="26" height="26" viewBox="0 0 24 24"><circle cx="12" cy="12" r="8" fill="none" stroke="#e3001b" stroke-width="4" stroke-dasharray="4 3"/><circle cx="12" cy="12" r="3" fill="#e3001b"/></svg></div><h3>Operating/Financial</h3><p>Sed ut perspiciatis unde omnis iste natus error sit volupta accus antium dolore.</p><span class="more">READ MORE ›</span></div>
    <div class="service"><div class="service-icon"><svg width="26" height="26" viewBox="0 0 24 24"><rect x="3" y="8" width="18" height="12" rx="2" fill="#e3001b"/><rect x="9" y="4" width="6" height="5" fill="none" stroke="#e3001b" stroke-width="2"/></svg></div><h3>Business Continuity</h3><p>Sed ut perspiciatis unde omnis iste natus error sit volupta accus antium dolore.</p><span class="more">READ MORE ›</span></div>
    <div class="service"><div class="service-icon"><svg width="26" height="26" viewBox="0 0 24 24"><path d="M12 3a9 9 0 1 0 9 9h-3a6 6 0 1 1-6-6V3z" fill="#e3001b"/><path d="M12 1l5 4-5 4z" fill="#e3001b"/></svg></div><h3>Disaster Recovery Plan</h3><p>Sed ut perspiciatis unde omnis iste natus error sit volupta accus antium dolore.</p><span class="more">READ MORE ›</span></div>
  </div>
</section>

<section class="about">
  <svg class="abs" style="left:0;top:0" width="1200" height="70" viewBox="0 0 1200 70" preserveAspectRatio="none"><path d="M0 0 L1200 0 L1200 20 Q600 90 0 20 Z" fill="#fff"/></svg>
  <div class="about-copy">
    <h4>ABOUT US</h4>
    <h2>VAULTMERROW</h2>
    <div class="divider"><span></span><i></i><span></span></div>
    <p>At vero eos et accusamus et iusto odio dignissimos ducimus qui blanditiis praesentium voluptatum deleniti atque corrupti quos dolores et quas molestias excepturi sint occaecati cupiditate non provident, similique sunt in culpa qui officia deserunt mollitia animi id est laborum et dolorum fuga. Et harum quidem rerum facilis est et expedita distinctio.</p>
    <span class="btn">Read More</span>
  </div>
  <div class="about-visual" role="img" aria-label="Photo of a smiling man in glasses working on a laptop, framed in a large shield shape"></div>
</section>

<section class="resources">
  <div class="resources-visual" role="img" aria-label="Photo of a hand holding a glowing blue digital security shield"></div>
  <div class="resources-copy">
    <h2>RESOURCES</h2>
    <div class="divider"><span></span><i></i><span></span></div>
    <p>At vero eos et accusamus et iusto odio dignissimos ducimus qui blanditiis praesentium voluptatum deleniti atque corrupti quos dolores et quas molestias excepturi sint occaecati cupiditate non provident, similique.</p>
    <ul class="resources-list">
      <li>Atque corrupti quos dolores et quas molestias</li>
      <li>Sed denounce with righteous indignation</li>
      <li>Nam libero tempore cum soluta nobis</li>
      <li>It is pleasure, but because those who</li>
      <li>Lorem Ipsum dolor sit amet, consectetur</li>
      <li>There are many variations of passages</li>
      <li>All the Lorem Ipsum generators</li>
      <li>Lorem Ipsum is simply dummy</li>
    </ul>
    <span class="btn">Read More</span>
  </div>
</section>

<section class="blog">
  <svg class="abs" style="left:0;top:0" width="1200" height="70" viewBox="0 0 1200 70" preserveAspectRatio="none"><path d="M0 0 L1200 0 L1200 20 Q600 90 0 20 Z" fill="#fff"/></svg>
  <h2 class="section-title">LATEST BLOG</h2>
  <div class="divider"><span></span><i></i><span></span></div>

  <div class="card" style="left:140px;top:192px;width:296px;height:400px;padding-top:222px">
    <div class="card-photo" role="img" aria-label="Photo of a person standing at a large window overlooking a city at dusk"></div>
    <h3>Contrary to popular belie Lorem Ipsum is not simply</h3>
    <p>Sed ut perspiciatis unde omnis iste natus error sit voluptatem.</p>
    <span class="btn-outline">Read More ›</span>
  </div>

  <div class="card" style="left:446px;top:192px;width:296px;height:260px">
    <div class="tag">Heading 1</div>
    <h3>Contrary to popular belie Lorem Ipsum is not simply</h3>
    <p>Sed ut perspiciatis unde omnis iste natus error sit voluptatem accus antium dolore tempor laud.</p>
    <span class="btn-outline">Read More ›</span>
  </div>

  <div class="card red" style="left:752px;top:192px;width:308px;height:260px;padding-top:40px">
    <h3>Lorem Ipsum is simply dummy text of the printing.</h3>
    <div style="margin-top:24px"><span class="btn-white">Read More ›</span></div>
  </div>

  <div class="card blue" style="left:140px;top:600px;width:296px;height:240px">
    <h3>Lorem Ipsum is simply dummy text</h3>
    <p>Sed ut perspiciatis unde omnis iste natus error sit voluptatem accus.</p>
    <span class="btn-ghost">Read More ›</span>
  </div>

  <div class="card dark" style="left:446px;top:460px;width:614px;height:380px;padding-top:56px">
    <h4>Lorem Ipsum</h4>
    <p style="margin:6px 0 0">Sed ut perspiciatis unde omnis iste natus</p>
    <h3>Lorem Ipsum is simply dum my text of the printing and typesetting industry</h3>
    <div style="margin-top:34px"><span class="btn-ghost">Read More ›</span></div>
  </div>

  <span class="btn view-all">View All Blog</span>
</section>

<section class="contact">
  <h2 class="section-title">CONTACT US</h2>
  <div class="divider"><span></span><i></i><span></span></div>

  <div class="info-card">
    <div class="map" role="img" aria-label="Street map showing the office location with a red pin"></div>
    <div class="map-label">
      <svg width="18" height="24" viewBox="0 0 24 32"><path d="M12 0a12 12 0 0 0-12 12c0 9 12 20 12 20s12-11 12-20A12 12 0 0 0 12 0z" fill="#e3001b"/><circle cx="12" cy="12" r="4" fill="#fff"/></svg>
      <span>4180 Harlow Creek Road<br>Marlow Springs, OR 97512</span>
    </div>
    <div class="info-row">
      <svg width="28" height="28" viewBox="0 0 24 24"><path d="M6.6 10.8a15 15 0 0 0 6.6 6.6l2.2-2.2c.3-.3.7-.4 1-.2 1.1.4 2.3.6 3.6.6.6 0 1 .4 1 1V20c0 .6-.4 1-1 1A17 17 0 0 1 3 4c0-.6.4-1 1-1h3.5c.6 0 1 .4 1 1 0 1.3.2 2.5.6 3.6.1.3 0 .7-.2 1z" fill="#e3001b"/></svg>
      <div>CALL US<br>000.000.0000</div>
    </div>
    <div class="info-row">
      <svg width="28" height="28" viewBox="0 0 24 24"><circle cx="12" cy="12" r="9" fill="none" stroke="#e3001b" stroke-width="2"/><path d="M12 7v5l3 2" stroke="#e3001b" stroke-width="2" fill="none"/></svg>
      <div>Our office hours<br>Monday to Friday from 8 A.M. to 6 P.M.</div>
    </div>
    <div class="info-row">
      <svg width="28" height="28" viewBox="0 0 24 24"><rect x="2" y="5" width="20" height="14" rx="2" fill="none" stroke="#e3001b" stroke-width="2"/><path d="M2 6l10 7 10-7" stroke="#e3001b" stroke-width="2" fill="none"/></svg>
      <div>E-mail Us : info@vaultmerrow.com.au</div>
    </div>
  </div>

  <div class="form-card">
    <h3>SEND MESSAGE</h3>
    <div class="divider"><span></span><i></i><span></span></div>
    <div class="field" style="margin-top:22px">Name</div>
    <div class="field">E-mail</div>
    <div class="field">Phone</div>
    <div class="field">Subject</div>
    <div class="field area">Message</div>
    <div class="submit">SUBMIT</div>
  </div>
</section>

<footer class="site-footer">
  <div class="footer-brand"><span class="brand-mark"></span><span class="brand-name">VAULTMERROW</span></div>
  <nav class="footer-nav"><span>HOME</span><span>|</span><span>SERVICES</span><span>|</span><span>ABOUT</span><span>|</span><span>RESOURCES</span><span>|</span><span>BLOG</span><span>|</span><span>CONTACT US</span></nav>
  <div class="footer-follow"><span>FOLLOW US</span><span class="social fb"></span><span class="social tw"></span></div>
  <div class="copyright">Copyright © 2018 All Rights Reserved</div>
</footer>

</body>
</html>
```